Redesign of business card for Cedar Ridge Mechanical

We are looking for a new design for our business cards for Cedar Ridge Mechanical. We are a plumbing & HVAC construction company, operating on the West Coast of Canada and USA. Logo attached.
Industry/Entity Type
Construction - Plumbing & HVAC
Contact Information for Business Card
Name, address, phone numbers, email, website address
Look and feel
Each slider illustrates characteristics of the customer's brand and the style your logo design should communicate.

```html
<!DOCTYPE html>
<html lang="en">
<head>
<meta charset="utf-8">
<title>Cedar Ridge Mechanical – Business Card</title>
<link rel="stylesheet" href="https://fonts.googleapis.com/css2?family=Poppins:wght@300;400;600&display=swap">
<style>
  :root {
    --stage: #2b2f34;
    --card: #1d1d1f;
    --card-edge: #111112;
    --ink: #f1f1f1;
    --ink-soft: #cfcfcf;
    --ghost: #2a2a2c;
    --emboss: #151516;
    --emboss-light: #2e2e31;
  }
  * { box-sizing: border-box; margin: 0; padding: 0; }
  html, body { width: 1200px; height: 780px; overflow: hidden; }
  body {
    background: var(--stage);
    font-family: "Poppins", sans-serif;
    display: flex;
    align-items: center;
    justify-content: center;
    gap: 40px;
  }
  .card {
    position: relative;
    width: 560px;
    height: 320px;
    border-radius: 18px;
    background: var(--card);
    box-shadow: 0 3px 0 var(--card-edge), 0 6px 0 var(--card-edge), 0 18px 30px rgba(0,0,0,.45);
    overflow: hidden;
  }

  /* Front */
  .ghost-mark {
    position: absolute;
    left: 40px; top: 70px;
    font-size: 34px;
    font-weight: 600;
    line-height: 1.05;
    color: var(--ghost);
    width: 220px;
  }
  .person { position: absolute; left: 44px; top: 64px; }
  .person-name { font-size: 28px; color: var(--ink); line-height: 1.1; }
  .person-name .first { font-weight: 600; }
  .person-name .last { font-weight: 300; }
  .person-title { font-size: 12px; font-weight: 400; color: var(--ink-soft); margin-top: 4px; }
  .divider {
    position: absolute;
    left: 170px; right: 0; top: 168px;
    height: 1.5px;
    background: var(--ink);
  }
  .brand {
    position: absolute;
    right: 40px; top: 60px;
    display: flex; align-items: center; gap: 12px;
  }
  .brand-square { width: 22px; height: 22px; background: var(--ink); }
  .brand-name {
    font-size: 19px; font-weight: 600; color: var(--ink);
    width: 170px; line-height: 1.15;
  }
  .contact {
    position: absolute;
    right: 34px; top: 186px;
    text-align: right;
    font-size: 13.5px; font-weight: 300; color: var(--ink);
    line-height: 1.45;
  }
  .contact-line { display: flex; justify-content: flex-end; align-items: center; gap: 10px; }
  .contact-line svg { width: 13px; height: 13px; fill: var(--ink); flex: none; }
  .contact-address { margin-right: 23px; }

  /* Back */
  .card-back { display: flex; align-items: center; justify-content: center; }
  .back-brand { display: flex; align-items: center; gap: 18px; }
  .back-square { width: 34px; height: 34px; background: var(--emboss); }
  .back-name {
    font-size: 34px; font-weight: 600; color: var(--emboss);
    line-height: 1.1; width: 270px;
  }
</style>
</head>
<body>

<section class="card card-front" aria-label="Business card front">
  <div class="ghost-mark" aria-hidden="true">Cedar Ridge Mechanical</div>

  <div class="person">
    <p class="person-name"><span class="first">Marta</span> <span class="last">Kovalenko</span></p>
    <p class="person-title">Founder &amp; CEO</p>
  </div>

  <div class="brand">
    <span class="brand-square"></span>
    <span class="brand-name">Cedar Ridge Mechanical</span>
  </div>

  <div class="divider"></div>

  <div class="contact">
    <p class="contact-address">418 Harbourline Rd. Suite 120<br>Bellingham, WA 98225</p>
    <p class="contact-line">(360) 555-0147
      <svg viewBox="0 0 24 24" aria-hidden="true"><path d="M6.6 10.8a15.1 15.1 0 0 0 6.6 6.6l2.2-2.2a1 1 0 0 1 1-.25 11.4 11.4 0 0 0 3.6.57 1 1 0 0 1 1 1V20a1 1 0 0 1-1 1A17 17 0 0 1 3 4a1 1 0 0 1 1-1h3.5a1 1 0 0 1 1 1c0 1.25.2 2.45.57 3.57a1 1 0 0 1-.25 1z"/></svg>
    </p>
    <p class="contact-line">info@cedarridgemech.com
      <svg viewBox="0 0 24 24" aria-hidden="true"><path d="M12 2a10 10 0 1 0 0 20 10 10 0 0 0 0-20zm6.9 6h-2.9a15.7 15.7 0 0 0-1.4-3.6A8 8 0 0 1 18.9 8zM12 4a14 14 0 0 1 1.9 4h-3.8A14 14 0 0 1 12 4zM4.3 14a8.2 8.2 0 0 1 0-4h3.4a16.5 16.5 0 0 0 0 4zm.8 2h2.9a15.7 15.7 0 0 0 1.4 3.6A8 8 0 0 1 5.1 16zM8 8H5.1a8 8 0 0 1 4.3-3.6A15.7 15.7 0 0 0 8 8zm4 12a14 14 0 0 1-1.9-4h3.8A14 14 0 0 1 12 20zm2.3-6H9.7a14.7 14.7 0 0 1 0-4h4.6a14.7 14.7 0 0 1 0 4zm.3 5.6A15.7 15.7 0 0 0 16 16h2.9a8 8 0 0 1-4.3 3.6zm1.7-5.6a16.5 16.5 0 0 0 0-4h3.4a8.2 8.2 0 0 1 0 4z"/></svg>
    </p>
    <p class="contact-line">www.cedarridgemech.com
      <svg viewBox="0 0 24 24" aria-hidden="true"><path d="M3 5h18a1 1 0 0 1 1 1v12a1 1 0 0 1-1 1H3a1 1 0 0 1-1-1V6a1 1 0 0 1 1-1zm1 2.3V17h16V7.3l-8 5.4zM5.6 7 12 11.3 18.4 7z"/></svg>
    </p>
  </div>
</section>

<section class="card card-back" aria-label="Business card back">
  <div class="back-brand">
    <span class="back-square"></span>
    <span class="back-name">Cedar Ridge Mechanical</span>
  </div>
</section>

</body>
</html>
```